Realty Group Needs Classy, Contemporary Letterhead Design

We need a letterhead design for a new realty company located in NY, USA. We buy investment properties to rehabilitate and or keep in our rental portfolio.

```html
<!DOCTYPE html>
<html lang="en">
<head>
<meta charset="utf-8">
<title>Meridian Realty Group – Letterhead</title>
<link href="https://fonts.googleapis.com/css2?family=Montserrat:wght@500;600&family=Source+Sans+3:wght@400&display=swap" rel="stylesheet">
<style>
  :root {
    --purple: #4b2a86;
    --band-gray: #808080;
    --text: #3f3f3f;
    --ink: #1c1c1c;
    --backdrop: #e1e1e1;
    --paper: #ffffff;
    --signature-tone: #ececec;
  }
  * { margin: 0; padding: 0; box-sizing: border-box; }
  html, body {
    width: 1200px; height: 1200px; overflow: hidden;
    background: var(--backdrop);
  }
  .letterhead {
    position: absolute; left: 204px; top: 40px;
    width: 792px; height: 1120px;
    background: var(--paper);
    font-family: "Source Sans 3", sans-serif;
    color: var(--text);
  }
  .edge-band {
    position: absolute; left: 0; top: 0; bottom: 0; width: 21px;
    background: var(--band-gray);
  }
  .edge-rule {
    position: absolute; left: 25px; top: 0; bottom: 0; width: 4px;
    background: var(--purple);
  }
  .brand {
    position: absolute; left: 76px; top: 100px;
    display: flex; align-items: center; gap: 12px;
  }
  .brand-mark {
    width: 24px; height: 24px; background: var(--purple);
  }
  .brand-name {
    font-weight: 400; font-size: 30px; line-height: 1;
    color: var(--purple);
  }
  .recipient {
    position: absolute; left: 74px; top: 232px;
    font-size: 15.5px; line-height: 21.4px; font-style: normal;
  }
  .salutation {
    position: absolute; left: 74px; top: 381px; font-size: 15.5px;
  }
  .body-copy {
    position: absolute; left: 74px; top: 424px; width: 643px;
    font-size: 15.5px; line-height: 21.3px; text-align: justify;
  }
  .signature {
    position: absolute; left: 479px; top: 772px; width: 229px; height: 58px;
    background: var(--signature-tone); border-radius: 4px;
  }
  .footer {
    position: absolute; left: 74px; top: 1032px; width: 638px;
    border-top: 1.5px solid var(--ink);
    font-family: "Montserrat", sans-serif; color: var(--ink);
  }
  .footer-address {
    margin-top: 7px; font-weight: 600; font-size: 12.5px;
  }
  .footer-contacts {
    display: flex; gap: 8px; margin-top: 5px;
    font-weight: 500; font-size: 11px; white-space: nowrap;
  }
  .contact { display: flex; align-items: center; gap: 3px; }
  .contact svg { width: 10px; height: 10px; fill: var(--purple); }
</style>
</head>
<body>
  <main class="letterhead">
    <div class="edge-band"></div>
    <div class="edge-rule"></div>

    <header class="brand">
      <span class="brand-mark"></span>
      <span class="brand-name">Meridian Realty Group, LLC</span>
    </header>

    <address class="recipient">
      Mr. Alan Reed<br>
      President<br>
      Northline Accountants<br>
      111 Street Name,<br>
      City State, 12345
    </address>

    <p class="salutation">Dear</p>

    <div class="body-copy">
      <p>Lorem ipsum dolor sit amet, consectetur adipiscing elit. Aenean ut ipsum eget massa hendrerit vestibulum vel in velit. Donec pretium neque velit.</p>
      <p>Aliquam porta lectus nec mauris ornare venenatis. Vivamus non est turpis, et cursus sem. Mauris vehicula erat in diam auctor at bibendum nisl lacinia.</p>
      <p>Morbi imperdiet neque vehicula nunc convallis gravida. Vestibulum iaculis pretium placerat. Integer consequat, est sit amet facilisis eleifend, nibh nibh varius orci, eget dapibus arcu dui non purus. Pellentesque in magna mauris. Duis enim sapien, dictum vitae condimentum a, pulvinar vel lacus. Mauris et molestie nibh. Vestibulum vitae nulla at metus elementum porta sit amet interdum elit. Nulla sollicitudin neque eu nulla volutpat congue.</p>
      <p>Etiam pellentesque, velit id dapibus fermentum, turpis sapien ornare dui, ac tincidunt ligula odio congue purus. Nunc sed ante dui, in porta lectus. Cras nec sem lorem. In hac habitasse platea dictumst. Maecenas id diam quis dui porta tristique. Sed id egestas felis. Donec ullamcorper mattis posuere. Phasellus fermentum eleifend tortor vel dapibus. Vestibulum ante ipsum.</p>
    </div>

    <div class="signature" role="img" aria-label="Handwritten signature of Daniel Harper"></div>

    <footer class="footer">
      <div class="footer-address">2150 Harbor View Ave, Suite 210 Albany NY 12207</div>
      <div class="footer-contacts">
        <span class="contact">
          <svg viewBox="0 0 10 10"><path d="M2 0.5 L3.6 2.6 L2.7 3.7 C3.3 5 4.9 6.6 6.3 7.3 L7.4 6.4 L9.5 8 L8.3 9.5 C4.5 9.3 0.7 5.5 0.5 1.7 Z"/></svg>555.010.1200
        </span>
        <span class="contact">
          <svg viewBox="0 0 10 10"><rect x="2.5" y="0.5" width="5" height="9" rx="1" fill="none" stroke="#1c1c1c" stroke-width="0.9"/></svg>555.020.1000
        </span>
        <span class="contact">
          <svg viewBox="0 0 10 10"><rect x="2.5" y="0.5" width="5" height="3"/><rect x="1" y="3.5" width="8" height="4" rx="0.8"/><rect x="2.5" y="7" width="5" height="2.5"/></svg>555.030.8046
        </span>
        <span class="contact">
          <svg viewBox="0 0 10 10"><rect x="0.5" y="2" width="9" height="6.5" rx="0.8"/><path d="M0.8 2.4 L5 5.6 L9.2 2.4" fill="none" stroke="#fff" stroke-width="0.9"/></svg>daniel@meridianrealty.com
        </span>
        <span class="contact">
          <svg viewBox="0 0 10 10"><g fill="none" stroke="#4b2a86" stroke-width="0.9"><circle cx="5" cy="5" r="4.3"/><ellipse cx="5" cy="5" rx="1.9" ry="4.3"/><path d="M0.7 5 H9.3 M1.5 2.8 H8.5 M1.5 7.2 H8.5"/></g></svg>www.meridianrealty.com
        </span>
      </div>
    </footer>
  </main>
</body>
</html>
```